Small Business Consulting Firm Needs Letterhead

We need a letterhead for our company "Brightpath Plus". Our company does outbound calling and mailing to business owner's companies who have taken high interest loans. These loans tend to put these businesses in a big financial bind short term, and we help them find better financial options. We would like the design to match our colors of our logo. Headers and footers would look nice, but we are open. We would want it to include our address, website, phone, and email info. Our address - 2000 E. Lamar Blvd. Suite 600Website - www.safeguardtoday.comEmail - info@safeguardtoday.comPhone - 855-726-1938
Industry/Entity Type
Financial Planning
Look and feel
Each slider illustrates characteristics of the customer's brand and the style your logo design should communicate.

```html
<!DOCTYPE html>
<html lang="en">
<head>
<meta charset="utf-8">
<title>Brightpath Plus Letterhead</title>
<link href="https://fonts.googleapis.com/css2?family=Lato:wght@400&display=swap" rel="stylesheet">
<style>
  :root {
    --backdrop: #3a3839;
    --paper: #ffffff;
    --blue-light: #1a85d0;
    --blue-dark: #1a5b9c;
    --green-light: #7cc142;
    --green-dark: #5e9e3e;
    --ink: #3d3d3f;
  }
  html, body {
    margin: 0;
    padding: 0;
    width: 1200px;
    height: 955px;
    overflow: hidden;
    background: var(--backdrop);
  }
  .letterhead {
    position: absolute;
    left: 278px;
    top: 27px;
    width: 643px;
    height: 900px;
    background: var(--paper);
    font-family: "Lato", sans-serif;
    color: var(--ink);
    box-shadow: 0 6px 24px rgba(0,0,0,0.35);
  }
  .stripe {
    position: absolute;
    display: flex;
  }
  .stripe span { flex: 1; }
  .stripe--header { left: 0; top: 85px; width: 424px; height: 16px; }
  .stripe--footer { right: 0; top: 859px; width: 409px; height: 13px; }
  .blue-light { background: var(--blue-light); }
  .blue-dark { background: var(--blue-dark); }
  .green-light { background: var(--green-light); }
  .green-dark { background: var(--green-dark); }

  .brand {
    position: absolute;
    right: 30px;
    top: 78px;
    display: flex;
    align-items: center;
    gap: 8px;
  }
  .brand__square {
    width: 12px;
    height: 12px;
    background: var(--blue-light);
  }
  .brand__name {
    font-size: 17px;
    letter-spacing: 1.5px;
    text-transform: uppercase;
    color: var(--ink);
  }

  .contact {
    position: absolute;
    left: 32px;
    top: 800px;
    margin: 0;
    padding: 0;
    list-style: none;
    font-size: 11px;
  }
  .contact li {
    display: flex;
    align-items: center;
    gap: 7px;
    height: 20px;
  }
  .contact svg { width: 15px; height: 15px; flex: none; }
</style>
</head>
<body>
  <main class="letterhead">
    <div class="stripe stripe--header">
      <span class="blue-light"></span><span class="blue-dark"></span><span class="green-light"></span><span class="green-dark"></span>
    </div>

    <div class="brand">
      <span class="brand__square"></span>
      <span class="brand__name">Brightpath Plus</span>
    </div>

    <ul class="contact">
      <li>
        <svg viewBox="0 0 16 16" aria-hidden="true"><circle cx="8" cy="8" r="8" fill="var(--blue-light)"/><path d="M5.2 4.2l1.6 0 .6 2-1 .8c.5 1.1 1.3 1.9 2.4 2.4l.8-1 2 .6v1.6c-3.8.3-6.7-2.6-6.4-6.4z" fill="#fff"/></svg>
        <span>855-726-1938</span>
      </li>
      <li>
        <svg viewBox="0 0 16 16" aria-hidden="true"><circle cx="8" cy="8" r="8" fill="var(--blue-dark)"/><rect x="4" y="5.2" width="8" height="5.6" fill="none" stroke="#fff" stroke-width="1"/><path d="M4 5.4l4 3 4-3" fill="none" stroke="#fff" stroke-width="1"/></svg>
        <span>info@brightpathplus.com</span>
      </li>
      <li>
        <svg viewBox="0 0 16 16" aria-hidden="true"><circle cx="8" cy="8" r="8" fill="var(--green-light)"/><circle cx="8" cy="8" r="4" fill="none" stroke="#fff" stroke-width=".9"/><path d="M4 8h8M8 4c-1.6 2.4-1.6 5.6 0 8M8 4c1.6 2.4 1.6 5.6 0 8" fill="none" stroke="#fff" stroke-width=".8"/></svg>
        <span>www.brightpathplus.com</span>
      </li>
      <li>
        <svg viewBox="0 0 16 16" aria-hidden="true"><circle cx="8" cy="8" r="8" fill="var(--green-dark)"/><path d="M8 12.5s-3.2-3.4-3.2-5.4a3.2 3.2 0 016.4 0c0 2-3.2 5.4-3.2 5.4z" fill="#fff"/><circle cx="8" cy="7.1" r="1.2" fill="var(--green-dark)"/></svg>
        <span>4170 W. Corwin Ave. Suite 310</span>
      </li>
    </ul>

    <div class="stripe stripe--footer">
      <span class="green-dark"></span><span class="green-light"></span><span class="blue-dark"></span><span class="blue-light"></span>
    </div>
  </main>
</body>
</html>
```